Business Cards Design for the electrical wholesaler: clean bold dynamic :)

We need a business card design that would follow our latest brand guidelines. As an electrical wholesaler we want to bring a fresh look and feel into the industry. The design should be clean bold and dynamic. It should come alive with the renewed energy of our green colour. Our grey colour should keep things balanced and complement the notion of maturity and responsibility. We employ Lato as a corporate font however are not bound by this font and we’re open to interpretation here.

Target Market(s)

Electrical contractors

Industry/Entity Type

Business

Contact Information for Business Card

Logo
Name & Surname: Halyna Dorosh
Job Title: Director of Marketing
Email: halya.dorosh@quillmail.example
Cell phone: XXX.XXX.XXXX
Address: 20517 - 87 Ave. Edmonton, AB, Canada. T6K 4N8
Business Phone: 780.555.0184
Website: www.brovix.example

Font styles to use
Other font styles liked:
• Lato

Requirements
Must have
• Logo & website
Nice to have
• Brand elements - some of them you may find in the attached Brand Guidelines (e.g. three lines on the background signifying "W")

```html
<!DOCTYPE html>
<html lang="en">
<head>
<meta charset="utf-8">
<title>Brovix Business Cards</title>
<link rel="stylesheet" href="https://fonts.googleapis.com/css2?family=Exo+2:wght@600&family=Roboto:wght@400;500&display=swap">
<style>
  :root {
    --bg: #c9c9c9;
    --green: #76b82a;
    --green-light: #7fbf22;
    --green-dark: #5fa22a;
    --band-green: rgba(60, 120, 30, 0.22);
    --band-grey: rgba(0, 0, 0, 0.045);
    --grey: #45494f;
    --grey-text: #55585c;
    --card-white: #f4f4f4;
    --card-white-edge: #e6e6e6;
  }
  * { margin: 0; padding: 0; box-sizing: border-box; }
  html, body { width: 1200px; height: 576px; overflow: hidden; }
  body {
    background: var(--bg);
    font-family: "Roboto", Arial, sans-serif;
    position: relative;
  }
  .card {
    position: absolute;
    top: 138px;
    width: 484px;
    height: 294px;
    border-radius: 13px;
    overflow: hidden;
    box-shadow: 0 3px 6px rgba(0,0,0,0.18);
  }
  .card--front {
    left: 82px;
    background: linear-gradient(160deg, var(--green-light) 0%, var(--green) 55%, var(--green-dark) 100%);
  }
  .card--back {
    left: 602px;
    width: 480px;
    background: linear-gradient(135deg, var(--card-white) 0%, #fafafa 50%, var(--card-white-edge) 100%);
  }
  .bands {
    position: absolute;
    inset: 0;
    width: 100%;
    height: 100%;
  }
  .bands--front path { fill: var(--band-green); }
  .bands--back path { fill: var(--band-grey); }
  .brand {
    position: absolute;
    display: flex;
    align-items: center;
    gap: 10px;
    font-family: "Roboto", Arial, sans-serif;
    font-weight: 500;
    color: var(--grey);
    letter-spacing: -0.5px;
    line-height: 1;
  }
  .brand__dot {
    width: 30px;
    height: 30px;
    border-radius: 50%;
    background: var(--grey);
  }
  .card--front .brand {
    left: 0; right: 0;
    top: 118px;
    justify-content: center;
    font-size: 46px;
  }
  .card--back .brand {
    right: 40px;
    top: 196px;
    font-size: 44px;
  }
  .card--back .brand__dot {
    width: 28px; height: 28px;
    background: var(--green);
  }
  .name-tab {
    position: absolute;
    left: -22px;
    top: 28px;
    width: 34px;
    height: 52px;
    border-radius: 50%;
    background: var(--green);
  }
  .holder__name {
    position: absolute;
    left: 29px;
    top: 37px;
    font-family: "Exo 2", Arial, sans-serif;
    font-weight: 600;
    font-size: 21px;
    color: var(--green);
    line-height: 1;
  }
  .holder__title {
    position: absolute;
    left: 29px;
    top: 62px;
    font-size: 11.5px;
    color: var(--grey-text);
  }
  .address {
    position: absolute;
    left: 28px;
    top: 192px;
    font-size: 12px;
    font-style: normal;
    line-height: 17px;
    color: var(--grey-text);
  }
  .contacts {
    position: absolute;
    left: 29px;
    top: 232px;
    font-size: 12px;
    color: var(--grey-text);
    list-style: none;
  }
  .contacts__row { display: flex; align-items: center; gap: 12px; height: 18px; margin-bottom: 3px; }
  .contact { display: flex; align-items: center; gap: 7px; white-space: nowrap; }
  .contact__icon { width: 12px; height: 12px; flex: none; }
</style>
</head>
<body>
  <section class="card card--front" aria-label="Card front">
    <svg class="bands bands--front" viewBox="0 0 484 294" preserveAspectRatio="none" aria-hidden="true">
      <path d="M160 30 H225 L300 294 H235 Z"/>
      <path d="M262 30 H327 L402 294 H337 Z"/>
      <path d="M364 30 H429 L504 294 H439 Z"/>
    </svg>
    <div class="brand"><span class="brand__dot"></span>brovix</div>
  </section>

  <section class="card card--back" aria-label="Card back">
    <svg class="bands bands--back" viewBox="0 0 480 294" preserveAspectRatio="none" aria-hidden="true">
      <path d="M180 30 H245 L320 294 H255 Z"/>
      <path d="M280 30 H345 L420 294 H355 Z"/>
      <path d="M380 30 H445 L520 294 H455 Z"/>
    </svg>
    <span class="name-tab"></span>
    <h1 class="holder__name">Halyna Dorosh</h1>
    <p class="holder__title">Director of Marketing</p>

    <address class="address">20517 - 87 Ave. Edmonton,<br>AB, Canada T6K 4N8</address>

    <ul class="contacts">
      <li class="contacts__row">
        <span class="contact">
          <svg class="contact__icon" viewBox="0 0 12 12" aria-hidden="true"><circle cx="6" cy="6" r="5.5" fill="#76b82a"/><path d="M3.4 4.2c.3 1.8 2.2 3.9 4.4 4.4l.8-1-1.1-.8-.6.5c-.9-.4-1.6-1.1-1.9-1.9l.5-.6-.8-1.1z" fill="#fff"/></svg>
          +1 780-555-0184
        </span>
      </li>
      <li class="contacts__row">
        <span class="contact">
          <svg class="contact__icon" viewBox="0 0 12 12" aria-hidden="true"><circle cx="6" cy="6" r="5.5" fill="#76b82a"/><rect x="3.2" y="4" width="5.6" height="4" fill="#fff"/><path d="M3.2 4 6 6.2 8.8 4" stroke="#76b82a" stroke-width="0.7" fill="none"/></svg>
          halya.dorosh@quillmail.example
        </span>
        <span class="contact">
          <svg class="contact__icon" viewBox="0 0 12 12" aria-hidden="true"><circle cx="6" cy="6" r="5.5" fill="#76b82a"/><circle cx="6" cy="6" r="2.8" fill="none" stroke="#fff" stroke-width="0.8"/><path d="M3.2 6h5.6M6 3.2c-1.2 1.5-1.2 4.1 0 5.6M6 3.2c1.2 1.5 1.2 4.1 0 5.6" stroke="#fff" stroke-width="0.6" fill="none"/></svg>
          www.brovix.example
        </span>
      </li>
    </ul>

    <div class="brand"><span class="brand__dot"></span>brovix</div>
  </section>
</body>
</html>
```